Brellwick Partners, LLC Stationary

Brellwick Partners, LLC is a new financial planning and consulting company. We are looking for designs on business cards, letterhead, envelopes, and anything else that would be useful. Our preference for business card design is two sided. We are looking for a professional and clean look with incorporating the logo and patriotic feel. Thank you to all who participate and good luck!

```html
<!DOCTYPE html>
<html lang="en">
<head>
<meta charset="utf-8">
<title>Brellwick Partners, LLC — Stationery</title>
<link rel="stylesheet" href="https://fonts.googleapis.com/css2?family=Source+Sans+3:wght@300;400;600&display=swap">
<style>
  :root {
    --navy: #143f6b;
    --red: #c42029;
    --backdrop: #e0e0e0;
    --paper: #ffffff;
    --ink: #3a3a3a;
    --muted: #8a8a8a;
    --ghost: #f3f3f3;
  }
  * { box-sizing: border-box; margin: 0; padding: 0; }
  html, body { width: 1200px; height: 1200px; overflow: hidden; }
  body {
    background: var(--backdrop);
    font-family: "Source Sans 3", "Source Sans Pro", Arial, sans-serif;
    color: var(--ink);
    position: relative;
  }
  .sheet { position: absolute; background: var(--paper); overflow: hidden; }

  .brand { display: flex; align-items: center; gap: 10px; color: var(--navy); font-weight: 600; white-space: nowrap; }
  .brand-mark { background: var(--red); flex: none; }

  /* Letterhead */
  .letterhead { left: 38px; top: 58px; width: 728px; height: 1020px; }
  .letterhead .band-top { position: absolute; left: 0; top: 0; width: 100%; height: 22px; background: var(--navy); }
  .letterhead .band-bottom { position: absolute; left: 0; bottom: 0; width: 100%; height: 22px; background: var(--red); }
  .letterhead .brand { position: absolute; left: 0; right: 0; top: 100px; justify-content: center; font-size: 30px; }
  .letterhead .brand-mark { width: 20px; height: 20px; }
  .letterhead .ghost { position: absolute; left: 185px; top: 400px; width: 340px; height: 340px; border-radius: 50%; background: var(--ghost); }
  .letterhead .footer { position: absolute; left: 0; right: 0; top: 956px; text-align: center; font-size: 10.5px; }
  .contact-row { display: flex; justify-content: center; gap: 14px; margin-top: 6px; }
  .contact-item { display: flex; align-items: center; gap: 5px; }
  .icon { background: var(--navy); border-radius: 2px; display: inline-flex; align-items: center; justify-content: center; flex: none; }
  .letterhead .icon { width: 10px; height: 10px; }

  /* Business card back */
  .card-back { left: 662px; top: 83px; width: 490px; height: 286px; background: var(--navy); }
  .card-back .brand { position: absolute; left: 0; right: 0; top: 126px; justify-content: center; color: var(--paper); font-size: 28px; }
  .card-back .brand-mark { width: 18px; height: 18px; }

  /* Business card front */
  .card-front { left: 662px; top: 382px; width: 490px; height: 284px; }
  .card-front .band-top { position: absolute; left: 0; top: 0; width: 100%; height: 20px; background: var(--navy); }
  .card-front .band-bottom { position: absolute; left: 0; bottom: 0; width: 100%; height: 20px; background: var(--red); }
  .card-front .ghost { position: absolute; left: 290px; top: 70px; width: 190px; height: 190px; border-radius: 50%; background: var(--ghost); }
  .card-front .brand { position: absolute; left: 24px; top: 54px; font-size: 22px; }
  .card-front .brand-mark { width: 14px; height: 14px; }
  .card-front .address { position: absolute; left: 21px; top: 133px; font-size: 12.5px; font-weight: 300; line-height: 16px; }
  .card-front .person { position: absolute; right: 22px; top: 128px; text-align: left; }
  .card-front .person-name { color: var(--navy); font-size: 16px; }
  .card-front .person-role { color: var(--muted); font-size: 12.5px; font-weight: 300; }
  .card-front .contacts { position: absolute; left: 21px; top: 188px; display: flex; flex-direction: column; gap: 3px; font-size: 12.5px; font-weight: 300; }
  .card-front .contact-item { gap: 13px; }
  .card-front .icon { width: 20px; height: 20px; }

  /* Envelope */
  .envelope { left: 544px; top: 775px; width: 627px; height: 381px; background: transparent; overflow: visible; }
  .envelope .flap { position: absolute; left: 0; top: 0; width: 627px; height: 96px; }
  .envelope .body { position: absolute; left: 0; top: 96px; width: 627px; height: 285px; background: var(--paper); }
  .envelope .band-bottom { position: absolute; left: 0; bottom: 0; width: 100%; height: 12px; background: var(--red); }
  .envelope .brand { position: absolute; left: 14px; top: 14px; font-size: 16px; gap: 7px; }
  .envelope .brand-mark { width: 11px; height: 11px; }
  .envelope .address { position: absolute; left: 53px; top: 60px; font-size: 8px; line-height: 11px; }
</style>
</head>
<body>

<section class="sheet letterhead">
  <div class="band-top"></div>
  <div class="ghost" aria-hidden="true"></div>
  <div class="brand"><span class="brand-mark"></span>BRELLWICK PARTNERS, LLC</div>
  <div class="footer">
    <p>418 Harlow Ave # 210, Kenton, GA 30118, USA</p>
    <div class="contact-row">
      <span class="contact-item"><span class="icon"><svg width="7" height="7" viewBox="0 0 10 10"><path d="M2 1h2l1 2-1 1a6 6 0 0 0 2 2l1-1 2 1v2c-4 0-7-3-7-7z" fill="#fff"/></svg></span>+1 555-014-2290</span>
      <span class="contact-item"><span class="icon"><svg width="7" height="7" viewBox="0 0 10 10"><rect x="1" y="2.5" width="8" height="5" fill="none" stroke="#fff"/><path d="M1 2.5l4 3 4-3" fill="none" stroke="#fff"/></svg></span>info@brellwickpartners.com</span>
      <span class="contact-item"><span class="icon"><svg width="7" height="7" viewBox="0 0 10 10"><circle cx="5" cy="5" r="4" fill="none" stroke="#fff"/><path d="M1 5h8M5 1v8" stroke="#fff"/></svg></span>www.brellwickpartners.com</span>
    </div>
  </div>
  <div class="band-bottom"></div>
</section>

<section class="sheet card-back">
  <div class="brand"><span class="brand-mark"></span>BRELLWICK PARTNERS, LLC</div>
</section>

<section class="sheet card-front">
  <div class="band-top"></div>
  <div class="ghost" aria-hidden="true"></div>
  <div class="brand"><span class="brand-mark"></span>BRELLWICK PARTNERS, LLC</div>
  <p class="address">418 Harlow Ave # 210, Kenton,<br>GA 30118, USA</p>
  <div class="person">
    <p class="person-name">Daniel Harper</p>
    <p class="person-role">Financial Advisor</p>
  </div>
  <div class="contacts">
    <span class="contact-item"><span class="icon"><svg width="13" height="13" viewBox="0 0 10 10"><path d="M2 1h2l1 2-1 1a6 6 0 0 0 2 2l1-1 2 1v2c-4 0-7-3-7-7z" fill="#fff"/></svg></span>+1 555-014-2290</span>
    <span class="contact-item"><span class="icon"><svg width="13" height="13" viewBox="0 0 10 10"><rect x="1" y="2.5" width="8" height="5" fill="none" stroke="#fff" stroke-width="0.8"/><path d="M1 2.5l4 3 4-3" fill="none" stroke="#fff" stroke-width="0.8"/></svg></span>info@brellwickpartners.com</span>
    <span class="contact-item"><span class="icon"><svg width="13" height="13" viewBox="0 0 10 10"><circle cx="5" cy="5" r="4" fill="none" stroke="#fff" stroke-width="0.8"/><ellipse cx="5" cy="5" rx="1.8" ry="4" fill="none" stroke="#fff" stroke-width="0.6"/><path d="M1 5h8" stroke="#fff" stroke-width="0.6"/></svg></span>www.brellwickpartners.com</span>
  </div>
  <div class="band-bottom"></div>
</section>

<section class="sheet envelope">
  <svg class="flap" viewBox="0 0 627 96" aria-hidden="true">
    <path d="M0 96 L26 10 Q29 0 40 0 H587 Q598 0 601 10 L627 96 Z" fill="var(--navy)"/>
  </svg>
  <div class="body">
    <div class="brand"><span class="brand-mark"></span>BRELLWICK PARTNERS, LLC</div>
    <p class="address">418 Harlow Ave # 210, Kenton,<br>GA 30118, USA</p>
    <div class="band-bottom"></div>
  </div>
</section>

</body>
</html>
```